Orvane Mechanical - Letterhead

We are a plumbing and hvac company based in Calgary. This letterhead will be on our quotes, invoices, preventative maintenance proposals etc.

```html
<!DOCTYPE html>
<html lang="en">
<head>
<meta charset="utf-8">
<title>Orvane Mechanical – Letterhead</title>
<link href="https://fonts.googleapis.com/css2?family=Open+Sans:wght@400;700;800&family=Arimo:wght@700&display=swap" rel="stylesheet">
<style>
  :root {
    --backdrop: #e2e3e3;
    --paper: #f9f9f9;
    --accent-orange: #e85323;
    --brand-blue: #2a6cb8;
    --ink: #3a3a3a;
    --ink-dark: #111111;
    --signature-tone: #dcdcdc;
  }
  html, body {
    margin: 0;
    width: 1200px;
    height: 945px;
    overflow: hidden;
    background: var(--backdrop);
  }
  .letterhead {
    position: absolute;
    left: 290px;
    top: 34px;
    width: 620px;
    height: 876px;
    background: var(--paper);
    box-shadow: 0 8px 24px rgba(0,0,0,0.12);
    font-family: "Open Sans", sans-serif;
    color: var(--ink);
  }
  .band {
    position: absolute;
    left: 87px;
    width: 464px;
    background: var(--accent-orange);
  }
  .band--top {
    top: 0;
    height: 12px;
    border-radius: 0 0 10px 10px;
  }
  .band--bottom {
    bottom: 0;
    height: 17px;
    border-radius: 12px 12px 0 0;
  }
  .brand {
    position: absolute;
    top: 66px;
    left: 0;
    right: 0;
    display: flex;
    justify-content: center;
    align-items: center;
    gap: 8px;
  }
  .brand__dot {
    width: 12px;
    height: 12px;
    border-radius: 50%;
    background: var(--accent-orange);
  }
  .brand__name {
    font-weight: 800;
    font-size: 20px;
    letter-spacing: 0.5px;
    color: var(--brand-blue);
    text-transform: uppercase;
  }
  .letter {
    position: absolute;
    top: 232px;
    left: 100px;
    right: 70px;
    font-size: 11px;
    line-height: 1.36;
  }
  .letter__greeting {
    font-family: "Arimo", sans-serif;
    font-weight: 700;
    font-size: 13px;
    color: var(--ink-dark);
    margin: 0 0 10px;
  }
  .letter p {
    margin: 0 0 14px;
  }
  .signature {
    position: absolute;
    top: 632px;
    left: 118px;
    width: 118px;
    height: 44px;
    border-radius: 4px;
    background: linear-gradient(90deg, #d6d6d6, #ececec);
  }
  .contact {
    position: absolute;
    right: 70px;
    bottom: 44px;
    text-align: right;
    font-size: 10px;
    line-height: 1.6;
    color: var(--ink);
  }
  .contact__row {
    display: flex;
    justify-content: flex-end;
    align-items: center;
    gap: 4px;
  }
  .contact__icon {
    width: 9px;
    height: 9px;
    fill: var(--brand-blue);
    margin-left: 6px;
  }
</style>
</head>
<body>
  <main class="letterhead">
    <div class="band band--top"></div>

    <header class="brand">
      <span class="brand__dot"></span>
      <span class="brand__name">Orvane Mechanical</span>
    </header>

    <section class="letter">
      <p class="letter__greeting">Dear Mr. Halden,</p>
      <p>Lorem Ipsum is simply dummy text of the printing and typesetting industry. Lorem Ipsum has been the industry's standard dummy text ever since the 1500s, when an unknown printer took a galley of type and scrambled it to make a type specimen book. It has survived not only five centuries, but also the leap into electronic typesetting, remaining essentially unchanged.</p>
      <p>The standard chunk of Lorem Ipsum used since the 1500s is reproduced below for those interested. Sections 1.10.32 and 1.10.33 from "de Rebus Aequis et Iniquis" by Varenus are also reproduced in their exact original form, accompanied by English versions from the 1914 translation by H. Rowley</p>
      <p>Lorem Ipsum is simply dummy text of the printing and typesetting industry. Lorem Ipsum has been the industry's standard dummy text ever since the 1500s, when an unknown printer took a galley of type and scrambled it to make a type specimen book. It has survived not only five centuries, but also the leap into electronic typesetting, remaining essentially unchanged. It was popularised in the</p>
      <p>The standard chunk of Lorem Ipsum used since the 1500s is reproduced below for those interested. Sections 1.10.32 and 1.10.33 from "de Rebus Aequis et Iniquis" by Varenus are also reproduced in their exact original form, accompanied by English versions from the 1914 translation by H. Rowley</p>
    </section>

    <div class="signature" role="img" aria-label="Handwritten signature of the sender"></div>

    <footer class="contact">
      <div class="contact__row">PO Box 218, 7 Kestrel Way, Calgary, AB T2X 0A0</div>
      <div class="contact__row">
        <svg class="contact__icon" viewBox="0 0 10 10" aria-hidden="true"><path d="M2 0.5 L3.6 2.6 L2.8 3.6 Q4 6 6.4 7.2 L7.4 6.4 L9.5 8 L8.4 9.5 Q4.5 9.3 0.5 1.6 Z"/></svg>
        <span>403-555-0187</span>
        <svg class="contact__icon" viewBox="0 0 10 10" aria-hidden="true"><path d="M0 2 H10 V8 H0 Z M0.8 2.6 L5 5.6 L9.2 2.6" stroke="#fff" stroke-width="0.8"/></svg>
        <span>info@orvanemechanical.com</span>
        <svg class="contact__icon" viewBox="0 0 10 10" aria-hidden="true"><circle cx="5" cy="5" r="4.6"/></svg>
        <span>www.orvanemechanical.com</span>
      </div>
    </footer>

    <div class="band band--bottom"></div>
  </main>
</body>
</html>
```